Quintel Packaging Business Card

Project Overview
We are seeking a modern, minimalist business card that effectively represents our company while making a bold and lasting impression. The design should reflect trust, professionalism, and innovation, reinforcing our expertise in custom plastic manufacturing for warehouse and distribution centers.

Provided Assets & Specifications
Logo: We will provide our official logo for integration into the design.
Design Files: Photoshop (PSD) files for our printing specifications will be supplied.

Card Size & Material:
Dimensions: 3.5" x 2"
Material: 1/8" Radius Plastic Business Cards with 1/8" Rounded Corners
Clear plastic background—the design should strategically incorporate transparency.
Orientation: The card should be designed in landscape format for a sleek and professional presentation.

Design Requirements:
Logo Prominence
The logo must be the focal point of the card.
Space should be used effectively to draw attention to the logo while maintaining a minimalist layout.

Clear Plastic Integration
The transparent background should create the illusion of blank space, enhancing the modern and high-quality feel.
Avoid any frosted effects—we do not want white areas to appear semi-transparent.

Minimalist & Impactful
Clean, structured, and easy to read at a glance.
Focus on sharp contrast to ensure legibility and visibility.
The design should instill confidence and reflect our role as a leading plastics manufacturer.

Color Palette & Contrast
Primary Colors: Blue, Black, White, and Grey
Use bold black or blue for text and key elements to ensure they stand out against the clear plastic.
Avoid light, pastel, or neon colors that may fade into the plastic background.
No frosted or semi-transparent white—we do not want a cloudy effect.

Typography & Information Hierarchy
Bold, modern typography—clear, professional, and highly legible.
The business card should highlight:
Company Logo (Primary Focus)
Full Name & Title
Phone Number
Email
Website

Brand Representation
The card should reflect our expertise in manufacturing high-quality custom plastics for large-scale packaging and distribution businesses.
Our clients rely on us to enhance their brand presence through custom plastic solutions, and our business cards should reinforce that sense of precision and trust.

Final Considerations
Utilize the clear plastic effectively to differentiate our brand from standard business cards.
Maintain a sleek, professional aesthetic while ensuring all text and elements remain legible.
The design should align with our industry, conveying reliability and innovation.
We look forward to seeing a design that captures our brand identity, maximizes the clear plastic medium, and makes a strong, professional impact on our clients.

```html
<!DOCTYPE html>
<html lang="en">
<head>
<meta charset="utf-8">
<title>Quintel Packaging Business Card</title>
<link href="https://fonts.googleapis.com/css2?family=Montserrat:wght@400;500;700&display=swap" rel="stylesheet">
<style>
  :root {
    --page-bg: #e6e3df;
    --clear-plastic: #f3f1ee;
    --clear-edge: #d6d2cc;
    --panel-black: #1c1c1c;
    --brand-teal: #1f7284;
    --ink-dark: #3a3a3a;
    --text-warm: #d9cdb8;
  }
  * { margin: 0; padding: 0; box-sizing: border-box; }
  html, body {
    width: 1200px;
    height: 1047px;
    overflow: hidden;
    background: var(--page-bg);
    font-family: "Montserrat", sans-serif;
  }
  .business-card {
    position: absolute;
    left: 100px;
    top: 238px;
    width: 1000px;
    height: 571px;
    border-radius: 26px;
    background: var(--clear-plastic);
    border: 1px solid var(--clear-edge);
    overflow: hidden;
  }
  .card-divider {
    position: absolute;
    left: 496px;
    top: 0;
    width: 4px;
    height: 100%;
    background: var(--brand-teal);
  }
  .info-panel {
    position: absolute;
    left: 506px;
    top: 0;
    right: 0;
    bottom: 0;
    background: var(--panel-black);
  }
  .brand-mark {
    position: absolute;
    left: 0;
    width: 496px;
    top: 0;
    height: 100%;
    display: flex;
    align-items: center;
    justify-content: center;
    gap: 16px;
  }
  .brand-square {
    width: 44px;
    height: 44px;
    background: var(--brand-teal);
    flex: none;
  }
  .brand-name {
    font-weight: 700;
    font-size: 33px;
    color: var(--ink-dark);
    white-space: nowrap;
  }
  .contact-block {
    position: absolute;
    left: 54px;
    top: 122px;
    color: var(--text-warm);
  }
  .person-name {
    font-weight: 700;
    font-size: 45px;
    letter-spacing: 1px;
    color: var(--brand-teal);
    line-height: 1.1;
  }
  .person-title {
    font-size: 26px;
    margin-top: 10px;
  }
  .address {
    font-size: 26px;
    line-height: 1.45;
    margin-top: 26px;
  }
  .contact-list {
    list-style: none;
    margin-top: 22px;
    font-size: 26px;
  }
  .contact-list li {
    display: flex;
    align-items: center;
    gap: 12px;
    height: 39px;
  }
  .contact-icon {
    width: 22px;
    height: 22px;
    fill: var(--brand-teal);
    flex: none;
  }
</style>
</head>
<body>
  <div class="business-card">
    <div class="brand-mark">
      <span class="brand-square"></span>
      <span class="brand-name">Quintel Packaging</span>
    </div>
    <div class="card-divider"></div>
    <div class="info-panel">
      <div class="contact-block">
        <h1 class="person-name">MARCUS HALE</h1>
        <p class="person-title">Managing Director</p>
        <p class="address">Your address, City<br>State, Zip 1234</p>
        <ul class="contact-list">
          <li>
            <svg class="contact-icon" viewBox="0 0 24 24" aria-hidden="true"><path d="M6.6 10.8a15 15 0 0 0 6.6 6.6l2.2-2.2a1 1 0 0 1 1-.25 11.4 11.4 0 0 0 3.6.57 1 1 0 0 1 1 1V20a1 1 0 0 1-1 1A17 17 0 0 1 3 4a1 1 0 0 1 1-1h3.5a1 1 0 0 1 1 1c0 1.25.2 2.45.57 3.57a1 1 0 0 1-.25 1z"/></svg>
            <span>123 456 789</span>
          </li>
          <li>
            <svg class="contact-icon" viewBox="0 0 24 24" aria-hidden="true"><path d="M2 5h20v2.2l-10 6.3L2 7.2z"/><path d="M2 9.6l10 6.3 10-6.3V19H2z"/></svg>
            <span>info@yourgmail.com</span>
          </li>
          <li>
            <svg class="contact-icon" viewBox="0 0 24 24" aria-hidden="true"><circle cx="12" cy="12" r="10"/><path d="M12 2v20M2 12h20" stroke="#1c1c1c" stroke-width="1.5" fill="none"/></svg>
            <span>www.yourwebsite.com</span>
          </li>
        </ul>
      </div>
    </div>
  </div>
</body>
</html>
```